Corvane Lending Partners. Professional and Established Company

A full service finance company specializing in obtaining capital for small business. Business Lending advisor, helping small business owners access the capital they need to launch, grow, or sustain their business. Many of our programs offer flexible guidelines to overcome common obstacles such as credit score, credit history, and time in business, financials, and industry type. Our streamlined funding process makes getting a business loan, business line of credit, stated income commercial real estate loan, a smooth and stress free experience.SOME OF THE MOST COMMON NEEDS FOR BUSINESS CAPITAL:• Working Capital• Debt Consolidations (loans, merchant cash advances, etc.)• Payroll• Operating Expenses• Inventory• Equipment Financing• Commercial Real Estate (Purchase, Fix & Flip, Rehab, Renovations)• Business Acquisitions• Business ExpansionWe like the websites:www.quillmorecf.com they are in the same industry and provide the same servicesWe are wanting to be able to update when we do press releases and such using Word Press. Our look should be very professional and we will be adding Our Team Professional Bios and Headshots.

Industry/Entity Type

Finance

Number of Pages Required

5+ page

Font styles to use
Serif
Sans Serif

Requirements
Must have
• We want to copy quillmorecf.com
• We need:
• Home Page
• About Us
• Loan Programs
• Loan Criteria
• News
• Apply Now
• Contact
Nice to have
• See quillmorecf.com
Should not have
• Need professional design. Nothing bright or abstract

```html
<!DOCTYPE html>
<html lang="en">
<head>
<meta charset="utf-8">
<title>Corvane Lending Partners</title>
<link href="https://fonts.googleapis.com/css2?family=Montserrat:wght@400;500;600;700&family=Raleway:wght@400;500;600&display=swap" rel="stylesheet">
<style>
:root{
  --blue:#1f6fb8;
  --navy:#123a6b;
  --deep:#0f2f5c;
  --ink:#333;
  --grey:#9a9a9a;
  --pale:#d7e6f6;
  --white:#fff;
}
*{margin:0;padding:0;box-sizing:border-box}
html,body{width:1200px;height:4235px;overflow:hidden}
body{position:relative;font-family:"Montserrat",sans-serif;color:var(--ink);background:var(--white)}
.abs{position:absolute}
.topbar{left:0;top:0;width:1200px;height:34px;background:var(--blue);color:var(--white);font-size:14px}
.topbar .contact{position:absolute;top:9px;font-style:italic;font-family:"Raleway",sans-serif}
.topbar .social{position:absolute;top:9px;width:16px;height:16px;background:var(--white);border-radius:2px}
.navbar{left:0;top:34px;width:1200px;height:73px;background:var(--white)}
.brand{left:62px;top:34px;width:215px;height:93px;background:var(--white);box-shadow:0 2px 8px rgba(0,0,0,.25);display:flex;align-items:center;justify-content:center;text-align:center;color:var(--navy);font-weight:600;font-size:19px;line-height:1.2;z-index:3}
.nav{left:361px;top:58px;display:flex;gap:27px;font-size:16px;color:var(--navy)}
.hero{left:0;top:107px;width:1200px;height:449px;background:linear-gradient(135deg,#3a3d42,#1c1f24 45%,#4a4d52)}
.hero h1{position:absolute;top:200px;width:1200px;text-align:center;color:var(--white);font-size:56px;font-weight:600}
.hero-sub{left:0;top:302px;width:1200px;text-align:center;color:var(--white);font-size:21px;font-weight:600;line-height:1.55}
.btn{top:429px;height:35px;border-radius:18px;font-size:15px;font-weight:600;display:flex;align-items:center;justify-content:center}
.btn-primary{left:449px;width:144px;background:var(--blue);color:var(--white)}
.btn-light{left:601px;width:140px;background:var(--white);color:var(--navy)}
.dots{left:1134px;top:183px;width:10px}
.video-cta{left:0;top:598px;width:1200px;text-align:center;font-size:36px;color:var(--navy);font-family:"Raleway",sans-serif;font-weight:500}
.video-cta span{color:var(--blue)}
.feature{height:297px}
.panel{background:linear-gradient(180deg,#1c4f8f,#153d72);color:var(--white)}
.panel h3{font-size:24px;font-weight:500;line-height:1.25;margin-bottom:22px}
.panel p{font-size:16px;line-height:1.7;font-family:"Raleway",sans-serif}
.panel a{display:block;margin-top:14px;color:#7fd13b;font-size:16px;text-decoration:underline}
.photo{}
.section-title{left:0;width:1200px;text-align:center;font-size:34px;color:var(--navy);font-weight:500}
.service{width:300px;text-align:center}
.service .brush{position:absolute;left:-30px;top:100px;width:360px;height:210px;background:radial-gradient(ellipse at center,var(--pale),rgba(215,230,246,0) 70%)}
.service .icon{position:relative;margin:0 auto;width:125px;height:125px}
.service h4{position:relative;margin-top:52px;font-size:27px;font-weight:600;color:var(--navy)}
.service p{position:relative;margin-top:12px;font-size:16px;line-height:1.7;font-family:"Raleway",sans-serif}
.service a{position:relative;display:inline-block;margin-top:8px;font-size:15px;color:var(--navy);text-decoration:underline}
.loan{width:400px;text-align:center}
.loan .img{height:300px}
.loan h4{font-size:22px;font-weight:500;color:var(--navy);margin-top:24px}
.loan p{font-size:16px;line-height:1.7;margin-top:4px;font-family:"Raleway",sans-serif}
.btn-outline{left:460px;top:2971px;width:283px;height:51px;border:2px solid var(--navy);border-radius:26px;display:flex;align-items:center;justify-content:center;font-size:21px;font-weight:500;color:var(--navy)}
.headshot{background:linear-gradient(160deg,#d9dde2,#9aa4ae)}
.member .name{font-size:27px;font-weight:600;color:var(--navy);line-height:1.05}
.member .role{font-size:19px;font-weight:600;color:var(--navy);margin-top:4px}
.member .sector{font-size:19px;font-weight:600;color:#b5b5b5;line-height:1.1}
.footer-line{left:60px;top:4004px;width:1080px;height:1px;background:#e2e2e2}
.footer-brand{left:500px;top:4033px;width:206px;height:90px;font-size:18px}
.footer-nav{left:0;top:4141px;width:1200px;display:flex;justify-content:center;font-size:15px;color:var(--navy)}
.footer-nav span{padding:0 14px;border-left:1px solid var(--navy);line-height:1}
.footer-nav span:first-child{border-left:none}
.bottombar{left:0;top:4190px;width:1200px;height:45px;background:var(--blue);color:var(--white);font-size:12px;display:flex;align-items:center;justify-content:center}
</style>
</head>
<body>

<div class="abs topbar">
  <svg class="abs" style="left:707px;top:10px" width="14" height="14" viewBox="0 0 24 24"><path fill="#fff" d="M6.6 10.8c1.4 2.8 3.8 5.1 6.6 6.6l2.2-2.2c.3-.3.7-.4 1-.2 1.1.4 2.3.6 3.6.6.6 0 1 .4 1 1V20c0 .6-.4 1-1 1C10.6 21 3 13.4 3 4c0-.6.4-1 1-1h3.5c.6 0 1 .4 1 1 0 1.3.2 2.5.6 3.6.1.3 0 .7-.2 1z"/></svg>
  <span class="contact" style="left:729px">555-010-4420</span>
  <svg class="abs" style="left:855px;top:12px" width="15" height="11" viewBox="0 0 15 11"><rect width="15" height="11" rx="1" fill="#fff"/><path d="M0 1l7.5 5L15 1" stroke="#1f6fb8" fill="none"/></svg>
  <span class="contact" style="left:878px">info@corvanelending.com</span>
  <span class="social" style="left:1042px"></span>
  <span class="social" style="left:1062px"></span>
  <span class="social" style="left:1082px"></span>
</div>

<div class="abs navbar"></div>
<div class="abs brand">Corvane Lending<br>Partners</div>
<nav class="abs nav"><span>Home</span><span>About us</span><span>Loan programs</span><span>Loan Criteria</span><span>News</span><span>Apply Now</span><span>Contact</span></nav>

<section class="abs hero" role="img" aria-label="Dim office desk with a hand using a tablet and glasses on papers">
  <h1 style="top:90px">Corvane Lending Partners</h1>
</section>
<p class="abs hero-sub">Lorem Ipsum is simply dummy text of the<br>printing and typesetting industry.</p>
<div class="abs btn btn-primary">Our Services</div>
<div class="abs btn btn-light">Contact us</div>
<svg class="abs dots" width="10" height="180" viewBox="0 0 10 180"><line x1="5" y1="5" x2="5" y2="175" stroke="#fff" stroke-opacity=".6"/><circle cx="5" cy="5" r="4" fill="#fff"/><circle cx="5" cy="48" r="3.5" fill="#2a2d32" stroke="#fff"/><circle cx="5" cy="91" r="3.5" fill="#2a2d32" stroke="#fff"/><circle cx="5" cy="134" r="3.5" fill="#2a2d32" stroke="#fff"/><circle cx="5" cy="175" r="3.5" fill="#2a2d32" stroke="#fff"/></svg>

<p class="abs video-cta"><span>Click here</span> for a comprehensive video of our services</p>

<div class="abs feature panel" style="left:0;top:678px;width:728px;padding:42px 60px 0 90px">
  <h3>Lorem Ipsum is simply dummy text of the printing and typesetting industry.</h3>
  <p>Lorem Ipsum has been the industry's standard dummy text ever since the 1500s, when an unknown printer took a galley of type and scrambled it to make a type specimen book. It has survived not only five centuries</p>
  <a>Read more</a>
</div>
<div class="abs feature photo" style="left:728px;top:678px;width:472px;background:linear-gradient(200deg,#e8eef5,#8fa6c2 50%,#34506f)" role="img" aria-label="Glass skyscrapers seen from below against the sky"></div>

<div class="abs feature photo" style="left:0;top:977px;width:395px;background:linear-gradient(160deg,#a9b7c2,#8a5a44 45%,#6d6f5a)" role="img" aria-label="Brick corner shop building on a tree-lined street"></div>
<div class="abs feature panel" style="left:395px;top:977px;width:805px;height:299px;padding:48px 90px 0 68px">
  <h3>Lorem Ipsum is simply dummy text of the printing and typesetting industry.</h3>
  <p>Lorem Ipsum has been the industry's standard dummy text ever since the 1500s, when an unknown printer took a galley of type and scrambled it to make a type specimen book. It has survived not only five centuries</p>
  <a>Read more</a>
</div>

<h2 class="abs section-title" style="top:1322px">OUR SERVICES</h2>

<div class="abs service" style="left:62px;top:1440px">
  <div class="brush"></div>
  <div class="icon" role="img" aria-label="Payroll icon of a banknote with rising bars"><svg width="125" height="125" viewBox="0 0 125 125"><rect x="10" y="60" width="105" height="60" rx="4" fill="none" stroke="#123a6b" stroke-width="6"/><circle cx="62" cy="90" r="18" fill="none" stroke="#123a6b" stroke-width="6"/><rect x="30" y="30" width="12" height="26" fill="#123a6b"/><rect x="52" y="18" width="12" height="38" fill="#123a6b"/><rect x="74" y="6" width="12" height="50" fill="#123a6b"/></svg></div>
  <h4>PAYROLL</h4>
  <p>Lorem Ipsum is simply<br>dummy text of the printing<br>and typesetting industry</p>
  <a>Read more</a>
</div>
<div class="abs service" style="left:451px;top:1440px">
  <div class="brush"></div>
  <div class="icon" role="img" aria-label="Inventory icon of a stocked storage chest"><svg width="125" height="125" viewBox="0 0 125 125"><rect x="8" y="45" width="109" height="72" rx="8" fill="none" stroke="#123a6b" stroke-width="6"/><line x1="8" y1="72" x2="117" y2="72" stroke="#123a6b" stroke-width="6"/><rect x="50" y="62" width="25" height="20" fill="#123a6b"/><path d="M30 40V25h65v15" fill="none" stroke="#123a6b" stroke-width="6"/></svg></div>
  <h4>INVENTORY</h4>
  <p>Lorem Ipsum is simply<br>dummy text of the printing<br>and typesetting industry</p>
  <a>Read more</a>
</div>
<div class="abs service" style="left:810px;top:1440px">
  <div class="brush"></div>
  <div class="icon" role="img" aria-label="Business expansion icon of a bar chart with an upward arrow"><svg width="125" height="125" viewBox="0 0 125 125"><rect x="14" y="85" width="16" height="32" fill="none" stroke="#123a6b" stroke-width="5"/><rect x="42" y="65" width="16" height="52" fill="none" stroke="#123a6b" stroke-width="5"/><rect x="70" y="50" width="16" height="67" fill="none" stroke="#123a6b" stroke-width="5"/><rect x="98" y="32" width="16" height="85" fill="none" stroke="#123a6b" stroke-width="5"/><polyline points="10,70 45,40 65,50 110,10" fill="none" stroke="#123a6b" stroke-width="5"/><polygon points="110,4 116,20 100,16" fill="#123a6b"/><line x1="6" y1="120" x2="120" y2="120" stroke="#123a6b" stroke-width="4"/></svg></div>
  <h4>BUISNESS EXPANSION</h4>
  <p>Lorem Ipsum is simply<br>dummy text of the printing<br>and typesetting industry</p>
  <a>Read more</a>
</div>

<svg class="abs" style="left:505px;top:1826px" width="190" height="14" viewBox="0 0 190 14"><line x1="5" y1="7" x2="185" y2="7" stroke="#bbb"/><circle cx="5" cy="7" r="4" fill="#123a6b"/><circle cx="50" cy="7" r="3.5" fill="#fff" stroke="#999"/><circle cx="95" cy="7" r="3.5" fill="#fff" stroke="#999"/><circle cx="140" cy="7" r="3.5" fill="#fff" stroke="#999"/><circle cx="185" cy="7" r="3.5" fill="#fff" stroke="#999"/></svg>

<h2 class="abs section-title" style="top:1898px">LOAN PROGRAMS</h2>

<div class="abs loan" style="left:0;top:2011px"><div class="img" style="background:linear-gradient(180deg,#9fc9ea,#3e7a2a 45%,#5a9a34)" role="img" aria-label="Open green field with trees under a blue sky"></div><h4>LAND LOANS</h4><p>We are one of a select few private<br>lenders to specialize in land loans...</p></div>
<div class="abs loan" style="left:400px;top:2011px"><div class="img" style="background:linear-gradient(135deg,#c7cdc9,#8c958f 50%,#d8ddd9)" role="img" aria-label="Stethoscope resting on banknotes"></div><h4>HOSPITALITY LOANS</h4><p>From independent to flagged resort hotels,<br>we have the experience to close fast...</p></div>
<div class="abs loan" style="left:800px;top:2011px"><div class="img" style="background:linear-gradient(150deg,#e9ecef,#b0b8c0 55%,#6f7780)" role="img" aria-label="Modern apartment building with balconies"></div><h4>MULTIFAMILY LOANS</h4><p>From 4-unit apartment buildings to garden<br>apartments andlarge hi-rises;<br>we have the money you need.</p></div>

<div class="abs loan" style="left:0;top:2496px"><div class="img" style="background:linear-gradient(180deg,#2f8fd8,#7da6c4 50%,#3b4e62)" role="img" aria-label="Industrial refinery towers under a blue sky"></div><h4>INDUSTRIAL LOANS</h4><p>We are one of a select few private<br>lenders to specialize in land loans...</p></div>
<div class="abs loan" style="left:400px;top:2496px"><div class="img" style="background:linear-gradient(160deg,#5a6673,#c9a56a 50%,#3d4650)" role="img" aria-label="Warehouse aisle with forklift and stacked shelves"></div><h4>WAREHOUSE LOANS</h4><p>From bridge loans for an acquisition or<br>expansion, we have the money you need...</p></div>
<div class="abs loan" style="left:800px;top:2496px"><div class="img" style="background:linear-gradient(135deg,#f2b21e,#e39b0c 60%,#c7830a)" role="img" aria-label="Row of yellow self storage lockers"></div><h4>SELF STORAGE LOANS</h4><p>Funding for your self-storage project needs,<br>we handle each deal with care...</p></div>

<div class="abs btn-outline">VIEW LOAN PROGRAMS</div>

<h2 class="abs section-title" style="top:3078px">OUR TEAM</h2>

<div class="abs headshot" style="left:299px;top:3213px;width:271px;height:269px" role="img" aria-label="Headshot of team leader"></div>
<div class="abs member" style="left:582px;top:3243px"><div class="name">NORA<br>VALE</div><div class="role">TEAM LEADER</div><div class="sector">FINANCIAL<br>SECTOR</div></div>

<div class="abs headshot" style="left:748px;top:3284px;width:192px;height:198px" role="img" aria-label="Headshot of team source"></div>
<div class="abs member" style="left:951px;top:3328px"><div class="name">OWEN<br>LIAO</div><div class="role">TEAM SOURCE</div><div class="sector">FINANCIAL<br>SECTOR</div></div>

<div class="abs headshot" style="left:119px;top:3482px;width:180px;height:183px" role="img" aria-label="Headshot of area manager"></div>
<div class="abs member" style="left:310px;top:3506px"><div class="name">NORA<br>VALE</div><div class="role">AREA MANAGER</div><div class="sector">FINANCIAL<br>SECTOR</div></div>

<div class="abs headshot" style="left:570px;top:3482px;width:178px;height:183px" role="img" aria-label="Headshot of senior analyst"></div>
<div class="abs member" style="left:760px;top:3506px"><div class="name">CLARA<br>HOLLIS</div><div class="role">SENIOR ANALYST</div><div class="sector">FINANCIAL<br>SECTOR</div></div>

<div class="abs headshot" style="left:350px;top:3665px;width:220px;height:215px" role="img" aria-label="Headshot of senior manager"></div>
<div class="abs member" style="left:582px;top:3701px"><div class="name">MARCUS<br>REED</div><div class="role">SENIOR MANAGER</div><div class="sector">FINANCIAL<br>SECTOR</div></div>

<div class="abs footer-line"></div>
<div class="abs brand footer-brand">Corvane Lending<br>Partners</div>
<nav class="abs footer-nav"><span>About Us</span><span>Loan Programs</span><span>Loan Criteria</span><span>Apply Now</span><span>News</span><span>Contact</span><span>Site Map</span></nav>
<footer class="abs bottombar">Copyrights 2018. All Rights are Reserved</footer>

</body>
</html>
```